Business Card for Orthopaedic Clinic.
Should have nice design, double sided that includes logo
Should include my name, my contact, my email, webpage. A QR code to scan business card.

please use dummy information for privacy reasons. I will provide my name, email, practice address once a winner is selected.

Target Market(s)

Future patients

Contact Information for Business Card

Name: Dr Oyel
Contact No: +65 69027314
Practice Address: Singapore
Email: doctor@pelvaro.com
Website: www.pelvaro.com

Colors
00a990

Requirements
Must have
• Logo and a nice colour scheme.
A QR Code for Contact Card.
Name
Contact
Practice Address
Email
Website.
Nice to have
• Nice colour scheme
Should not have
• Nothing too cluttered.

```html
<!DOCTYPE html>
<html lang="en">
<head>
<meta charset="utf-8">
<title>Pelvaro Orthopaedics – Stationery</title>
<link href="https://fonts.googleapis.com/css2?family=Montserrat:wght@400;600;700&family=Arimo:wght@400;700&display=swap" rel="stylesheet">
<style>
  :root{
    --teal:#4fb0ab;
    --slate:#555d66;
    --ink:#3d4248;
    --paper:#f4f4f4;
    --card:#f6f6f6;
    --stage:#e3e3e3;
  }
  *{box-sizing:border-box;margin:0;padding:0}
  html,body{width:1200px;height:1200px;overflow:hidden;background:var(--stage)}
  .stage{position:relative;width:1200px;height:1200px}

  /* ---------- letterhead ---------- */
  .letterhead{position:absolute;left:114px;top:142px;width:647px;height:915px;background:var(--paper);
    font-family:Arimo,Arial,sans-serif;color:var(--ink);font-size:9.4px;line-height:13px}
  .letterhead .edge{position:absolute;left:0;top:0;width:22px;height:915px}
  .brand{position:absolute;display:flex;align-items:center;font-family:Montserrat,sans-serif;font-weight:400;color:var(--slate)}
  .brand .mark{background:var(--teal);flex:none}
  .brand .name{display:flex;flex-direction:column;line-height:1}
  .letterhead .brand{left:71px;top:50px;gap:11px}
  .letterhead .brand .mark{width:42px;height:42px}
  .letterhead .brand .word{font-size:28px;letter-spacing:.5px}
  .letterhead .brand .sub{font-size:12.5px;letter-spacing:5.1px;margin-top:4px}
  .block{position:absolute;left:68px;width:538px}
  .letter-date{top:207px}
  .recipient{top:232px}
  .salutation{top:324px;font-weight:700}
  .body{position:absolute;left:68px;top:0;width:538px}
  .body p{position:absolute;left:0;width:538px;text-align:justify}
  .closing{top:650px}
  .signature{position:absolute;left:68px;top:680px;width:70px;height:18px;background:#d9dcdf;border-radius:3px}
  .signer{top:716px}
  .footer-rule{position:absolute;top:858px;width:1px;height:57px;background:var(--teal)}
  .footer-item{position:absolute;top:869px;display:flex;align-items:center;gap:3px;
    font-family:Montserrat,sans-serif;font-size:10.5px;letter-spacing:.6px;color:var(--slate)}
  .footer-item svg{width:9px;height:9px;fill:var(--teal)}

  /* ---------- business cards ---------- */
  .card{position:absolute;left:814px;width:273px;height:157px}
  .card-front{top:207px;background:var(--teal)}
  .card-front .brand{left:51px;top:61px;gap:8px;color:#fff}
  .card-front .brand .mark{width:33px;height:33px;background:#fff}
  .card-front .brand .word{font-size:22px;letter-spacing:.4px}
  .card-front .brand .sub{font-size:10px;letter-spacing:3.6px;margin-top:3px}

  .card-back{top:422px;background:var(--card);overflow:hidden}
  .card-back .edge{position:absolute;left:0;top:0;width:9px;height:157px}
  .card-back .brand{left:27px;top:19px;gap:6px}
  .card-back .brand .mark{width:25px;height:25px}
  .card-back .brand .word{font-size:17px}
  .card-back .brand .sub{font-size:7.5px;letter-spacing:2.8px;margin-top:2px}
  .holder-rule{position:absolute;left:27px;top:91px;width:180px;height:1px;background:var(--teal)}
  .holder-name{position:absolute;right:20px;top:85px;font-family:Montserrat,sans-serif;font-weight:700;font-size:10.5px;color:var(--teal)}
  .contact-list{position:absolute;left:27px;top:104px;list-style:none;font-family:Montserrat,sans-serif;font-size:7px;line-height:9.2px;color:var(--slate)}
  .contact-list li{display:flex;align-items:center;gap:4px}
  .contact-list svg{width:6px;height:6px;fill:var(--teal)}
</style>
</head>
<body>
<svg width="0" height="0" style="position:absolute">
  <symbol id="i-pin" viewBox="0 0 10 10"><path d="M5 0a3.6 3.6 0 0 0-3.6 3.6C1.4 6.300 5 10 5 10s3.6-3.7 3.6-6.4A3.6 3.6 0 0 0 5 0zm0 5a1.4 1.4 0 1 1 0-2.8A1.4 1.4 0 0 1 5 5z"/></symbol>
  <symbol id="i-phone" viewBox="0 0 10 10"><path d="M2 .3l1.6 2.2-.9 1.1a6 6 0 0 0 3.7 3.7l1.1-.9 2.2 1.6-.8 1.6C4.8 9.8.2 5.2.4 1.1z"/></symbol>
  <symbol id="i-mail" viewBox="0 0 10 10"><path d="M.5 2h9v6h-9zm1 1v.3L5 5.6l3.5-2.3V3zm0 1.5V7h7V4.5L5 6.8z"/></symbol>
  <symbol id="i-web" viewBox="0 0 10 10"><path d="M5 .5a4.5 4.5 0 1 0 0 9 4.5 4.5 0 0 0 0-9zm3.4 4H7A7 7 0 0 0 6.3 1.7a3.5 3.5 0 0 1 2.1 2.8zM5 1.6c.5.7.9 1.7 1 2.9H4c.1-1.2.5-2.2 1-2.9zM3.7 1.7A7 7 0 0 0 3 4.5H1.6a3.5 3.5 0 0 1 2.1-2.8zM1.6 5.5H3a7 7 0 0 0 .7 2.8 3.5 3.5 0 0 1-2.1-2.8zM5 8.4c-.5-.7-.9-1.7-1-2.9h2c-.1 1.2-.5 2.2-1 2.9zm1.3-.1A7 7 0 0 0 7 5.5h1.4a3.5 3.5 0 0 1-2.1 2.8z"/></symbol>
</svg>

<main class="stage">
  <section class="letterhead">
    <svg class="edge" viewBox="0 0 22 915" preserveAspectRatio="none" aria-hidden="true">
      <rect width="22" height="915" fill="var(--teal)"/>
      <polygon points="0,0 22,0 22,113 0,101" fill="var(--slate)"/>
      <polygon points="0,101 22,113 22,116 0,104" fill="#fff"/>
    </svg>
    <div class="brand"><span class="mark"></span><span class="name"><span class="word">PELVARO</span><span class="sub">ORTHOPAEDICS</span></span></div>

    <p class="block letter-date">December 25, 2020</p>
    <p class="block recipient">Mr. John Doe<br>President<br>AA Corporation<br>111 Street Name, Suite#<br>City, State, 12345</p>
    <p class="block salutation">Dear Mr. John,</p>

    <div class="body">
      <p style="top:363px">Lorem ipsum dolor sit amet, consectetur adipiscing elit. Integer diam quam, egestas eu ultrices eu, suscipit ac sapien. Phasellus eu dui nisi. Nam et euismod diam, nec lobortis tortor. Donec et diam nulla. Aenean varius tincidunt convallis. Aliquam a tortor at lacus dictum aliquet. Nunc laoreet metus sapien, in scelerisque augue consectetur in.</p>
      <p style="top:416px">Fusce nec justo laoreet, egestas justo sed, aliquet sem. Pellentesque pharetra massa non orci bibendum semper. Pellentesque cursus eu lectus a consectetur. Nunc volutpat suscipit posuere. Vestibulum facilisis vel quam malesuada mattis. Nulla in mattis tellus. Maecenas tristique mauris vitae pharetra tincidunt. In ut ornare risus. Integer molestie vestibulum nisi, semper dapibus mi condimentum eu.</p>
      <p style="top:480px">Nullam sagittis elit libero, id fringilla est tincidunt eget. Donec in ipsum ultricies, consectetur quam vel, facilisis elit. Phasellus tincidunt congue risus vel luctus. Suspendisse ut mollis neque. Donec ornare orci in turpis vestibulum, in ultrices metus scelerisque. Pellentesque mattis mattis nunc, nec tincidunt lacus egestas id. Fusce facilisis sagittis neque sit amet vulputate. Aliquam ut eros lobortis tortor facilisis vehicula. Sed sed luctus leo, at laoreet sapien. Donec placerat adipiscing ligula non euismod. In lobortis pretium nisl id luctus.</p>
      <p style="top:559px">Integer gravida tincidunt nibh, scelerisque tincidunt turpis. Suspendisse potenti. Nunc hendrerit euismod lectus id elementum. Fusce vitae gravida velit, quis eleifend lectus. In imperdiet mauris eu dui viverra sagittis. Donec tempor dui diam, condimentum gravida lacus pretium a. Nullam fringilla augue quis arcu placerat scelerisque. Aliquam nec tincidunt augue, sit amet posuere ipsum.</p>
    </div>

    <p class="block closing">Sincerely Yours,</p>
    <div class="signature" role="img" aria-label="Handwritten signature of Dr Oyel"></div>
    <p class="block signer">Dr. Oyel<br>President</p>

    <span class="footer-rule" style="left:160px"></span>
    <span class="footer-rule" style="left:273px"></span>
    <span class="footer-rule" style="left:454px"></span>
    <span class="footer-item" style="left:68px"><svg><use href="#i-pin"/></svg>SINGAPORE</span>
    <span class="footer-item" style="left:171px"><svg><use href="#i-phone"/></svg>+65 69027314</span>
    <span class="footer-item" style="left:285px"><svg><use href="#i-mail"/></svg>doctor@pelvaro.com</span>
    <span class="footer-item" style="left:465px"><svg><use href="#i-web"/></svg>www.pelvaro.com</span>
  </section>

  <section class="card card-front">
    <div class="brand"><span class="mark"></span><span class="name"><span class="word">PELVARO</span><span class="sub">ORTHOPAEDICS</span></span></div>
  </section>

  <section class="card card-back">
    <svg class="edge" viewBox="0 0 9 157" preserveAspectRatio="none" aria-hidden="true">
      <rect width="9" height="157" fill="var(--teal)"/>
      <polygon points="0,95 9,100 9,157 0,157" fill="var(--slate)"/>
    </svg>
    <div class="brand"><span class="mark"></span><span class="name"><span class="word">PELVARO</span><span class="sub">ORTHOPAEDICS</span></span></div>
    <span class="holder-rule"></span>
    <span class="holder-name">Dr Oyel</span>
    <ul class="contact-list">
      <li><svg><use href="#i-phone"/></svg>+65 69027314</li>
      <li><svg><use href="#i-mail"/></svg>doctor@pelvaro.com</li>
      <li><svg><use href="#i-web"/></svg>www.pelvaro.com</li>
      <li><svg><use href="#i-pin"/></svg>SINGAPORE</li>
    </ul>
  </section>
</main>
</body>
</html>
```